Velvet Lantern rebranding my business with a new business card

I have my new logo and now I need a refresher on my business cards. I really want something fun and fresh. I like black background or anything to make the color pop.
Logo
Name: Velvet Lantern
Contact Info as stated below:
Mira Pellow
555-013-4762
Logo
Name: Velvet Lantern
Mira Pellow
555-013-4762
fb.me/VelvetLanternbyMira
Instagram: @VelvetLanternbyMira

Industry/Entity Type

Business

Contact Information for Business Card

double-sided. Logo on one side. Contact info on the other.

Requirements
Must have
• Logo
• Name: Velvet Lantern
• Contact Info as stated below:
• Mira Pellow
• 555-013-4762
• fb.me/VelvetLanternbyMira
• fb.me/VelvetLanternbyMira

```html
<!DOCTYPE html>
<html lang="en">
<head>
<meta charset="utf-8">
<title>Velvet Lantern – Business Card</title>
<link rel="stylesheet" href="https://fonts.googleapis.com/css2?family=Source+Sans+3:wght@400;600&display=swap">
<style>
  :root {
    --backdrop: #ece9e4;
    --kraft-light: #cfb088;
    --kraft-mid: #c3a275;
    --kraft-dark: #ad8b5f;
    --ink: #141210;
  }
  * { margin: 0; padding: 0; box-sizing: border-box; }
  html, body {
    width: 1200px;
    height: 900px;
    overflow: hidden;
    background: var(--backdrop);
    font-family: "Source Sans 3", "Myriad Pro", Arial, sans-serif;
    color: var(--ink);
  }
  .canvas { position: relative; width: 1200px; height: 900px; }
  .card {
    position: absolute;
    width: 556px;
    height: 342px;
    background: radial-gradient(ellipse at 30% 20%, var(--kraft-light), var(--kraft-mid) 55%, var(--kraft-dark));
    box-shadow: 0 2px 6px rgba(0,0,0,.15);
  }
  .card--front { left: 238px; top: 62px; }
  .card--back { left: 458px; top: 518px; }

  .contact {
    position: absolute;
    left: 0; right: 0; top: 93px;
    text-align: center;
  }
  .contact__name {
    font-size: 22px;
    font-weight: 600;
    letter-spacing: .2px;
    margin-bottom: 30px;
  }
  .contact__list { list-style: none; font-size: 15px; line-height: 23px; }

  .brand {
    position: absolute;
    inset: 0;
    display: flex;
    align-items: center;
    justify-content: center;
    gap: 10px;
  }
  .brand__dot {
    width: 14px; height: 14px;
    border-radius: 50%;
    background: var(--ink);
  }
  .brand__name {
    font-size: 26px;
    font-weight: 600;
    letter-spacing: .5px;
  }
</style>
</head>
<body>
<main class="canvas">
  <section class="card card--front" aria-label="Card front: contact details">
    <div class="contact">
      <h1 class="contact__name">Mira Pellow</h1>
      <ul class="contact__list">
        <li>555-013-4762</li>
        <li>info@velvetlantern.com</li>
        <li>www.velvetlantern.com</li>
        <li>fb.me/VelvetLanternbyMira</li>
      </ul>
    </div>
  </section>

  <section class="card card--back" aria-label="Card back: brand mark">
    <div class="brand">
      <span class="brand__dot"></span>
      <span class="brand__name">Velvet Lantern</span>
    </div>
  </section>
</main>
</body>
</html>
```